Website re-design for Brightmoor LLC website ( has existing website )

Looking to do a complete re-design of Brightmoorllc. The existing website is dated and built in wordpress. The new website will not be wordpress. The project folder includes an overview.txt file with details on the project. The file also contains a list of websites that he/she likes which I am sure is very helpful .
Number of Pages Required
1 page

```html
<!DOCTYPE html>
<html lang="en">
<head>
<meta charset="utf-8">
<title>Brightmoor – Keeping Your Shoreline Clean And Pristine</title>
<link rel="stylesheet" href="https://fonts.googleapis.com/css2?family=Poppins:wght@400;500;600;700&family=Open+Sans:ital,wght@0,400;0,600;1,400&display=swap">
<style>
:root{
  --blue:#0f6fbf;
  --blue-dark:#0b5aa0;
  --orange:#ff6a0d;
  --ink:#1b1b1b;
  --muted:#555;
  --footer:#0b141d;
  --white:#fff;
}
*{box-sizing:border-box;margin:0;padding:0}
html,body{width:1200px;height:3543px;overflow:hidden}
body{position:relative;font-family:"Open Sans",sans-serif;color:var(--ink);background:var(--white)}
.abs{position:absolute}
h1,h2,h3,h4,.poppins{font-family:"Poppins",sans-serif}

/* header */
.site-header{position:absolute;left:0;top:0;width:1200px;height:106px;background:#fff}
.brand{position:absolute;left:24px;top:12px;display:flex;align-items:center;gap:12px}
.brand-dot{width:84px;height:84px;border-radius:50%;background:var(--blue)}
.brand-name{font-family:"Poppins",sans-serif;font-size:38px;font-weight:400;color:var(--blue)}
.info{position:absolute;top:16px;display:flex;gap:14px;align-items:center}
.info .ring{width:52px;height:52px;border-radius:50%;border:2px solid var(--orange);display:flex;align-items:center;justify-content:center}
.info .ring span{width:40px;height:40px;border-radius:50%;background:var(--blue);display:flex;align-items:center;justify-content:center}
.info .label{font-family:"Poppins",sans-serif;font-size:15px;font-weight:600;color:var(--blue)}
.info .value{font-family:"Poppins",sans-serif;font-size:18px;color:var(--ink);line-height:26px}
.vsep{position:absolute;top:42px;width:1px;height:24px;background:#bbb}
.social-top{position:absolute;left:866px;top:34px;display:flex;gap:8px}
.social-top span{width:42px;height:42px;border-radius:50%;border:2px solid var(--blue)}
.search{position:absolute;left:1056px;top:40px;width:106px;border-bottom:1px solid #ccc;font-size:14px;color:#333;padding-bottom:6px}
.search svg{position:absolute;right:2px;top:4px}

/* nav */
.main-nav{position:absolute;left:0;top:106px;width:1200px;height:69px;background:var(--blue)}
.main-nav a{position:absolute;top:24px;font-family:"Poppins",sans-serif;font-size:16px;font-weight:500;color:#fff;text-decoration:none}
.cta-appt{position:absolute;right:0;top:0;width:282px;height:69px;background:var(--orange);clip-path:polygon(14px 0,100% 0,100% 100%,0 100%);font-family:"Poppins",sans-serif;font-weight:600;font-size:16px;color:#fff;display:flex;align-items:center;justify-content:center;padding-left:10px}

/* hero */
.hero-photo{position:absolute;left:0;top:175px;width:1200px;height:660px;background:linear-gradient(160deg,#5f7a3a 0%,#4d6a32 35%,#3f5430 65%,#5a5e42 100%)}
.hero-ring{position:absolute;left:131px;top:237px;width:460px;height:460px;border-radius:50%;border:4px solid #fff}
.hero-circle{position:absolute;left:143px;top:249px;width:436px;height:436px;border-radius:50%;background:var(--blue);text-align:center;color:#fff}
.hero-circle .welcome{margin-top:104px;font-family:"Poppins",sans-serif;font-size:36px}
.hero-circle h1{font-size:70px;font-weight:600;line-height:76px}
.hero-circle p{font-size:18px;margin-top:12px}
.btn{display:inline-block;background:var(--orange);color:#fff;font-family:"Poppins",sans-serif;font-weight:600;border-radius:30px}
.hero-circle .btn{margin-top:26px;font-size:16px;padding:14px 29px}
.dots{position:absolute;display:flex;gap:6px;align-items:center}
.dots i{width:10px;height:10px;border-radius:50%;background:#fff;display:block}
.dots i.on{width:14px;height:14px;border:3px solid #fff;background:var(--blue)}

/* section titles */
.title{position:absolute;left:0;width:1200px;text-align:center;font-family:"Poppins",sans-serif;font-size:31px;font-weight:500}
.title::after{content:"";display:block;width:42px;height:3px;background:var(--blue);margin:10px auto 0}

/* services */
.services-bg{position:absolute;left:0;top:835px;width:1200px;height:643px;background:#fbfbfb}
.card{position:absolute;top:997px;width:312px;height:378px}
.card .sheet{position:absolute;left:0;top:28px;width:312px;height:350px;background:#fff;clip-path:polygon(0 76px,100% 0,100% 100%,0 100%);box-shadow:0 4px 16px rgba(0,0,0,.08)}
.card .icon{position:absolute;left:92px;top:0;width:128px;height:128px;border-radius:50%;display:flex;align-items:center;justify-content:center}
.card h3{position:absolute;left:0;top:148px;width:312px;text-align:center;font-size:22px;font-weight:500;line-height:36px}
.card p{position:absolute;left:26px;top:238px;width:260px;text-align:center;font-size:15px;line-height:26px;color:#333}
.card .corner{position:absolute;right:0;bottom:0;width:52px;height:50px;clip-path:polygon(100% 0,100% 100%,0 100%);display:flex;align-items:flex-end;justify-content:flex-end;padding:0 10px 6px 0}
.arrow-btn{position:absolute;width:54px;height:54px;border-radius:50%;display:flex;align-items:center;justify-content:center}

/* about */
.about{position:absolute;left:0;top:1478px;width:1200px;height:429px;background:var(--blue)}
.about-photo{position:absolute;left:0;top:0;width:1200px;height:429px}
.about h2{position:absolute;left:112px;top:64px;font-size:31px;font-weight:500;color:#fff}
.about p{position:absolute;left:112px;top:128px;width:438px;color:#fff;font-size:14.5px;line-height:26.6px;text-align:justify}
.about .btn{position:absolute;left:112px;top:317px;font-size:15px;padding:13px 30px}

/* gallery */
.compare{position:absolute;top:2080px;width:475px;height:344px}
.compare .half{position:absolute;top:0;width:236px;height:344px;display:flex;align-items:center;justify-content:center;font-family:"Poppins",sans-serif;font-weight:600;font-size:30px;color:#fff}
.compare .handle{position:absolute;left:206px;top:141px;width:62px;height:62px;border-radius:50%;border:3px solid #fff}
.compare .line{position:absolute;left:236px;top:0;width:3px;height:344px;background:#fff}

/* testimonials */
.testimonials{position:absolute;left:0;top:2557px;width:1200px;height:560px;background:linear-gradient(180deg,#1a6aa8 0%,#1a5f9a 60%,#174f85 100%)}
.testimonials .title{color:#fff;top:95px}
.testimonials .title::after{background:#fff}
.quote-card{position:absolute;left:286px;top:159px;width:628px;height:277px;background:#fff;border-radius:6px;text-align:center}
.quote-card .q{font-style:italic;font-size:15px;line-height:27px;color:#333;margin:52px 48px 0}
.quote-card h4{font-size:20px;font-weight:500;margin-top:20px}
.quote-card .place{font-size:15px;color:#888;margin-top:6px}

/* footer */
.site-footer{position:absolute;left:0;top:3100px;width:1200px;height:443px;background:var(--footer);color:#fff}
.fcol{position:absolute;top:110px}
.fcol h4{font-size:19px;font-weight:500;margin-bottom:22px}
.fcol li{list-style:none;font-size:15.5px;line-height:25.5px}
.contact-row{display:flex;gap:12px;font-size:15.5px;line-height:25px;margin-bottom:18px}
.newsletter{display:flex;margin-top:0}
.newsletter .field{width:180px;height:44px;background:#fff;color:#777;font-size:14px;padding:12px 12px;border-radius:3px 0 0 3px}
.newsletter .go{width:56px;height:44px;background:var(--blue);display:flex;align-items:center;justify-content:center;border-radius:0 3px 3px 0}
.social-foot{display:flex;gap:16px;margin-top:40px}
.social-foot span{width:44px;height:44px;border-radius:50%;border:2px solid var(--blue);display:block}
.social-foot span.fill{background:var(--blue)}
.footer-rule{position:absolute;left:112px;top:377px;width:976px;height:1px;background:#26313c}
.copyright{position:absolute;left:0;top:398px;width:1200px;text-align:center;font-size:15.5px}
</style>
</head>
<body>

<header class="site-header">
  <div class="brand"><span class="brand-dot"></span><span class="brand-name">Brightmoor</span></div>

  <div class="info" style="left:352px">
    <div class="ring"><span><svg width="20" height="20" viewBox="0 0 24 24" fill="#fff"><path d="M6.6 10.8a15 15 0 0 0 6.6 6.6l2.2-2.2a1 1 0 0 1 1-.25 11.4 11.4 0 0 0 3.6.57 1 1 0 0 1 1 1V20a1 1 0 0 1-1 1A17 17 0 0 1 3 4a1 1 0 0 1 1-1h3.5a1 1 0 0 1 1 1c0 1.25.2 2.45.57 3.6a1 1 0 0 1-.25 1z"/></svg></span></div>
    <div><div class="label">Address</div><div class="value">4418 Birchwood Lane<br>Marlow Bay, MN 55390</div></div>
  </div>
  <span class="vsep" style="left:598px"></span>

  <div class="info" style="left:626px;top:30px">
    <div class="ring"><span><svg width="20" height="20" viewBox="0 0 24 24" fill="#fff"><path d="M6.6 10.8a15 15 0 0 0 6.6 6.6l2.2-2.2a1 1 0 0 1 1-.25 11.4 11.4 0 0 0 3.6.57 1 1 0 0 1 1 1V20a1 1 0 0 1-1 1A17 17 0 0 1 3 4a1 1 0 0 1 1-1h3.5a1 1 0 0 1 1 1c0 1.25.2 2.45.57 3.6a1 1 0 0 1-.25 1z"/></svg></span></div>
    <div><div class="label">Call Us Today!</div><div class="value">(555) 014-2280</div></div>
  </div>
  <span class="vsep" style="left:838px"></span>

  <div class="social-top"><span></span><span></span><span></span></div>
  <span class="vsep" style="left:1030px"></span>
  <div class="search">Search<svg width="13" height="13" viewBox="0 0 24 24" fill="none" stroke="#999" stroke-width="3"><circle cx="10" cy="10" r="7"/><path d="M15 15l6 6"/></svg></div>
</header>

<nav class="main-nav">
  <a style="left:46px">Home</a>
  <a style="left:130px">Services</a>
  <a style="left:231px">About Us</a>
  <a style="left:340px">Contact Us</a>
  <a style="left:460px">FAQ</a>
  <a style="left:531px">Employment</a>
  <a style="left:665px">Testimonials</a>
  <a style="left:800px">Gallery</a>
  <div class="cta-appt">Schedule An Appoinment</div>
</nav>

<section class="hero">
  <div class="hero-photo" role="img" aria-label="Two scuba divers wading among lily pads near a dock"></div>
  <div class="hero-ring"></div>
  <div class="hero-circle">
    <div class="welcome">Welcome To</div>
    <h1>Brightmoor</h1>
    <p>Keeping Your Shoreline Clean And Pristine</p>
    <span class="btn">Get Started</span>
  </div>
  <div class="dots" style="left:578px;top:757px"><i></i><i class="on"></i><i></i></div>
  <svg class="abs" style="left:0;top:735px" width="1200" height="110" viewBox="0 0 1200 110" preserveAspectRatio="none">
    <path d="M0 72 C120 20 220 10 330 30 C470 55 560 80 700 78 C880 76 1000 40 1200 0 L1200 110 L0 110Z" fill="var(--blue)"/>
    <path d="M0 82 C120 30 220 22 330 42 C470 66 560 92 700 90 C880 88 1000 54 1200 14 L1200 110 L0 110Z" fill="#fbfbfb"/>
  </svg>
</section>

<section class="services">
  <div class="services-bg"></div>
  <h2 class="title" style="top:895px">Our Services</h2>

  <div class="arrow-btn" style="left:36px;top:1191px;background:#fff;box-shadow:0 2px 8px rgba(0,0,0,.12)"><svg width="14" height="14" viewBox="0 0 24 24" fill="none" stroke="var(--orange)" stroke-width="3"><path d="M15 4l-8 8 8 8"/></svg></div>
  <div class="arrow-btn" style="left:1112px;top:1191px;background:var(--orange)"><svg width="14" height="14" viewBox="0 0 24 24" fill="none" stroke="#fff" stroke-width="3"><path d="M9 4l8 8-8 8"/></svg></div>

  <article class="card" style="left:111px">
    <div class="sheet"></div>
    <div class="icon" style="background:var(--blue)"><svg width="64" height="64" viewBox="0 0 64 64" fill="none" stroke="#fff" stroke-width="2.5"><circle cx="36" cy="10" r="4"/><path d="M20 18h28M30 22l6 10-8 6M14 40h20v12H14z"/><path d="M8 50c4-3 8-3 12 0s8 3 12 0 8-3 12 0 8 3 12 0"/><path d="M8 56c4-3 8-3 12 0s8 3 12 0 8-3 12 0 8 3 12 0"/></svg></div>
    <h3>Water Trampoline<br>Management</h3>
    <p>From installation at the start of the season to removal at the end of the season to winter storage, we've got you covered with this service.</p>
    <div class="corner" style="background:var(--blue)"><svg width="16" height="10" viewBox="0 0 16 10" fill="none" stroke="#fff" stroke-width="1.6"><path d="M0 5h15M11 1l4 4-4 4"/></svg></div>
  </article>

  <article class="card" style="left:444px">
    <div class="sheet"></div>
    <div class="icon" style="background:var(--orange)"><svg width="64" height="64" viewBox="0 0 64 64" fill="none" stroke="#fff" stroke-width="2.5"><rect x="6" y="22" width="38" height="18" rx="7"/><path d="M25 28v6M50 8v40l-8 8H30"/><path d="M50 18h6M50 28h6"/></svg></div>
    <h3>Zebra Mussel<br>removal</h3>
    <p>This Invasive species is becoming an increasing risk to Minnesota waterways. These sharp mussels build up on swim ladders, irrigation</p>
    <div class="corner" style="background:var(--orange)"><svg width="16" height="10" viewBox="0 0 16 10" fill="none" stroke="#fff" stroke-width="1.6"><path d="M0 5h15M11 1l4 4-4 4"/></svg></div>
  </article>

  <article class="card" style="left:776px">
    <div class="sheet"></div>
    <div class="icon" style="background:var(--blue)"><svg width="60" height="60" viewBox="0 0 64 64" fill="none" stroke="#fff" stroke-width="3"><circle cx="26" cy="26" r="16"/><path d="M38 38l16 16M18 22a9 9 0 0 1 8-6"/></svg></div>
    <h3>Lost Item<br>Search</h3>
    <p>Have you dropped something of value in the water? From boat keys to tools to other items, our scuba divers scour the bottom to recover</p>
    <div class="corner" style="background:var(--blue)"><svg width="16" height="10" viewBox="0 0 16 10" fill="none" stroke="#fff" stroke-width="1.6"><path d="M0 5h15M11 1l4 4-4 4"/></svg></div>
  </article>
</section>

<section class="about">
  <svg class="about-photo" width="1200" height="429" viewBox="0 0 1200 429">
    <defs><linearGradient id="lakeTone" x1="0" y1="0" x2="0" y2="1"><stop offset="0" stop-color="#5b94d6"/><stop offset=".45" stop-color="#3d78bf"/><stop offset=".55" stop-color="#2c4f78"/><stop offset="1" stop-color="#1d3550"/></linearGradient></defs>
    <path d="M593 0 C640 70 600 140 588 200 C575 270 640 330 598 429 L1200 429 L1200 0Z" fill="var(--orange)"/>
    <path d="M606 0 C650 70 612 140 600 200 C588 270 652 330 610 429 L1200 429 L1200 0Z" fill="url(#lakeTone)" role="img" aria-label="Photo of a wooden dock with an empty boat lift frame on a blue lake"/>
  </svg>
  <h2>About Us</h2>
  <p>Brightmoor LLC is a company formed in response to the increasing incidence of invasive species in Minnesota's lakes and water systems. The impact of these fast-growing nuisances, inspired our venture to effectively control unwanted lake weeds. Brightmoor, LLC helps provide the enjoyable weed-free lake environment craved by water enthusiasts.</p>
  <span class="btn">LEARN MORE</span>
</section>

<section class="gallery">
  <h2 class="title" style="top:1983px">Our Gallery</h2>

  <div class="compare" style="left:111px">
    <div class="half" style="left:0;background:linear-gradient(180deg,#7d8a92 0%,#8f8a6e 45%,#7a6a45 100%)" role="img" aria-label="Shoreline covered with floating weeds before cleanup">Before</div>
    <div class="half" style="left:239px;background:linear-gradient(180deg,#a9b4bd 0%,#8e9aa3 30%,#5a6670 45%,#8a969e 100%)" role="img" aria-label="Clear lake water after cleanup">After</div>
    <div class="line"></div><div class="handle"></div>
  </div>
  <div class="compare" style="left:613px">
    <div class="half" style="left:0;background:linear-gradient(180deg,#9fa8a2 0%,#4f6a35 30%,#857a66 70%,#6e6458 100%)" role="img" aria-label="Dock with weeds piled on the boards before cleanup">Before</div>
    <div class="half" style="left:239px;background:linear-gradient(180deg,#3e5a2c 0%,#587040 35%,#9b8f80 70%,#7d7468 100%)" role="img" aria-label="Clean dock after weed removal">After</div>
    <div class="line"></div><div class="handle"></div>
  </div>
  <svg class="abs" style="left:318px;top:2438px" width="60" height="30" viewBox="0 0 60 30" fill="none" stroke="#555" stroke-width="2.5"><path d="M4 4c6 24 34 26 48 10M44 12l8 2 0-8"/></svg>
  <svg class="abs" style="left:820px;top:2438px" width="60" height="30" viewBox="0 0 60 30" fill="none" stroke="#555" stroke-width="2.5"><path d="M4 4c6 24 34 26 48 10M44 12l8 2 0-8"/></svg>
</section>

<section class="testimonials" role="img" aria-label="Underwater blue backdrop">
  <h2 class="title">Our Testimonials</h2>
  <div class="quote-card">
    <svg class="abs" style="left:46px;top:-24px" width="56" height="46" viewBox="0 0 56 46" fill="var(--blue)"><path d="M0 46V26C0 12 8 2 22 0v8c-7 2-10 7-10 14h10v24zM32 46V26C32 12 40 2 54 0v8c-7 2-10 7-10 14h10v24z"/></svg>
    <p class="q">"Everyone used to jump off the water trampoline and instantly get tangled in lake weeds. We contacted Brightmoor and their SCUBA divers have now been solving our problem for the past 4 years!"</p>
    <h4>Hollis Pines Association</h4>
    <div class="place">Lake Wrenfield</div>
    <div class="dots" style="left:291px;top:234px"><i style="background:#ccc"></i><i style="background:var(--blue)"></i><i style="background:#ccc"></i></div>
  </div>
</section>

<svg class="abs" style="left:0;top:3040px" width="1200" height="70" viewBox="0 0 1200 70" preserveAspectRatio="none">
  <path d="M0 20 C120 60 200 70 300 40 C420 8 520 0 620 14 C760 32 900 50 1200 40 L1200 70 L0 70Z" fill="#fff"/>
  <path d="M0 28 C120 68 200 78 300 48 C420 16 520 8 620 22 C760 40 900 58 1200 48 L1200 70 L0 70Z" fill="var(--footer)"/>
</svg>

<footer class="site-footer">
  <div class="fcol" style="left:112px">
    <h4>QUICK LINKS</h4>
    <ul><li>Home</li><li>Services</li><li>About Us</li><li>Contact Us</li><li>FAQ</li><li>Employment</li><li>Testimonials</li><li>Gallery</li></ul>
  </div>
  <div class="fcol" style="left:343px">
    <h4>QUICK LINKS</h4>
    <ul><li>Terms &amp; Conditions</li><li>Privacy Policy</li><li>About Us</li><li>Support</li></ul>
  </div>
  <div class="fcol" style="left:586px">
    <h4>CONTACT US</h4>
    <div class="contact-row"><svg width="15" height="20" viewBox="0 0 24 32" fill="#fff"><path d="M12 0C5.4 0 0 5.4 0 12c0 9 12 20 12 20s12-11 12-20C24 5.4 18.6 0 12 0zm0 17a5 5 0 1 1 0-10 5 5 0 0 1 0 10z"/></svg><span>4418 Birchwood Lane<br>Marlow Bay, MN 55390</span></div>
    <div class="contact-row"><svg width="16" height="16" viewBox="0 0 24 24" fill="#fff"><path d="M6.6 10.8a15 15 0 0 0 6.6 6.6l2.2-2.2a1 1 0 0 1 1-.25 11.4 11.4 0 0 0 3.6.57 1 1 0 0 1 1 1V20a1 1 0 0 1-1 1A17 17 0 0 1 3 4a1 1 0 0 1 1-1h3.5a1 1 0 0 1 1 1c0 1.25.2 2.45.57 3.6a1 1 0 0 1-.25 1z"/></svg><span>(555) 014-2280</span></div>
    <div class="contact-row"><svg width="16" height="16" viewBox="0 0 24 24" fill="#fff"><path d="M2 5h20v14H2z"/><path d="M2 5l10 8 10-8" stroke="var(--footer)" stroke-width="2" fill="none"/></svg><span>info@brightmoor.com</span></div>
  </div>
  <div class="fcol" style="left:840px">
    <h4>SIGN UP FOR NEWSLETTER</h4>
    <div class="newsletter"><div class="field">Email Address</div><div class="go"><svg width="18" height="14" viewBox="0 0 24 18" fill="#fff"><path d="M0 0h24v18H0z"/><path d="M0 0l12 9 12-9" stroke="var(--blue)" stroke-width="2" fill="none"/></svg></div></div>
    <div class="social-foot"><span></span><span class="fill"></span><span></span><span></span></div>
  </div>
  <div class="footer-rule"></div>
  <div class="copyright">©Copyrights 2022 Brightmoor &nbsp;&nbsp;|&nbsp;&nbsp; All Rights Reserved</div>
</footer>

</body>
</html>
```